RTavenor Business Cards & Letterhead

I have a logo but need a design for some new business cards. We are a Design-Build Firm that specializes in the design and construction of commercial projects.
the cards need to be professional. no cartoon stuff.
i would like to have the cards in AI format so I can update the card as needed. Logo is provided.
Our Address is: 4187 Marlowe Ct. Brookfield, Ohio 27614

```html
<!DOCTYPE html>
<html lang="en">
<head>
<meta charset="utf-8">
<title>RTavenor Business Card</title>
<link rel="stylesheet" href="https://fonts.googleapis.com/css2?family=Open+Sans:wght@400;600;800&display=swap">
<style>
  :root {
    --backdrop: #131313;
    --paper: #fcfcf1;
    --brand-blue: #155a93;
    --brand-blue-light: #1a7cc0;
    --brand-blue-dark: #0d3d6a;
    --ink: #1e1e1e;
    --ink-grey: #58585a;
  }
  * { box-sizing: border-box; margin: 0; padding: 0; }
  html, body { width: 1200px; height: 780px; overflow: hidden; }
  body {
    background: var(--backdrop);
    font-family: "Open Sans", Arial, sans-serif;
    position: relative;
  }
  .card {
    position: absolute;
    top: 230px;
    width: 560px;
    height: 320px;
    background: var(--paper);
    overflow: hidden;
  }
  .card--back { left: 30px; }
  .card--front { left: 610px; }

  .colour-band {
    position: absolute;
    top: 70px;
    height: 180px;
    background: linear-gradient(135deg, var(--brand-blue-light), var(--brand-blue-dark));
  }
  .card--back .colour-band { right: 0; width: 110px; }
  .card--front .colour-band { left: 0; width: 150px; }

  .wordmark {
    position: absolute;
    display: flex;
    align-items: center;
    gap: 8px;
    font-weight: 800;
    letter-spacing: 1px;
    text-transform: uppercase;
  }
  .wordmark__square { width: 20px; height: 20px; background: var(--brand-blue); }
  .card--back .wordmark { left: 36px; bottom: 34px; font-size: 34px; color: var(--ink-grey); }
  .card--front .wordmark { right: 34px; top: 26px; font-size: 30px; color: var(--brand-blue); }
  .card--front .wordmark__square { width: 18px; height: 18px; }

  .accent-bar {
    position: absolute;
    top: 0;
    right: 0;
    width: 16px;
    height: 90px;
    background: linear-gradient(180deg, var(--brand-blue-light), var(--brand-blue-dark));
  }

  .contact {
    position: absolute;
    right: 34px;
    top: 92px;
    text-align: right;
    color: var(--ink);
    font-size: 14px;
    line-height: 1.35;
  }
  .contact__name {
    font-size: 20px;
    font-weight: 800;
    color: var(--brand-blue);
    text-transform: uppercase;
    letter-spacing: 0.5px;
  }
  .contact__title { font-size: 14px; margin-bottom: 10px; }
  .contact__address { margin-bottom: 12px; }
  .contact__line { display: flex; justify-content: flex-end; align-items: center; gap: 6px; }
  .contact__line svg { width: 12px; height: 12px; flex: none; }
</style>
</head>
<body>
  <section class="card card--back">
    <div class="colour-band"></div>
    <div class="wordmark"><span class="wordmark__square"></span>RTavenor</div>
  </section>

  <section class="card card--front">
    <div class="colour-band"></div>
    <div class="accent-bar"></div>
    <div class="wordmark"><span class="wordmark__square"></span>RTavenor</div>
    <div class="contact">
      <p class="contact__name">Marcus Tavenor</p>
      <p class="contact__title">Founder/President</p>
      <p class="contact__address">4187 Marlowe Ct. Brookfield,<br>Ohio 27614</p>
      <p class="contact__line">(740) 555-0148
        <svg viewBox="0 0 12 12"><circle cx="6" cy="6" r="6" fill="#155a93"/><path d="M3.5 3.2c.4-.4.9-.3 1.1.1l.5.9c.1.3 0 .6-.2.8l-.3.3c.3.7.9 1.3 1.6 1.6l.3-.3c.2-.2.5-.3.8-.2l.9.5c.4.2.5.7.1 1.1-.7.7-2 .4-3.3-.9S2.8 3.9 3.5 3.2z" fill="#fff"/></svg>
      </p>
      <p class="contact__line">www.rtavenor.com
        <svg viewBox="0 0 12 12"><circle cx="6" cy="6" r="6" fill="#155a93"/><circle cx="6" cy="6" r="3.6" fill="none" stroke="#fff" stroke-width="0.9"/><path d="M2.4 6h7.2M6 2.4c-1.6 2-1.6 5.2 0 7.2M6 2.4c1.6 2 1.6 5.2 0 7.2" fill="none" stroke="#fff" stroke-width="0.8"/></svg>
      </p>
      <p class="contact__line">MRT@RTavenor.com
        <svg viewBox="0 0 12 12"><rect width="12" height="12" rx="2" fill="#155a93"/><rect x="2.5" y="3.5" width="7" height="5" fill="none" stroke="#fff" stroke-width="0.9"/><path d="M2.5 3.5L6 6.3l3.5-2.8" fill="none" stroke="#fff" stroke-width="0.9"/></svg>
      </p>
    </div>
  </section>
</body>
</html>
```